Wordpress Design Project for Bankruptcy Law Office in San Francisco

our current website: www.dorvanelilaw-example.com

we would like to re-design it for wordpress to make it faster and a bit more modern.

content should be similar to what we have there right now but also we do family law

please include logo for law office:

Law Office of Marta K. Dolvenidze

Thank you.
Updates

please see attached word document with logos that we like as an example.

we do tend to like color red.  darker red.

Please submit your design variations and logo as soon as possible.   We would like to go over them and make our decision

Reason: Please create couple of more variations of logo for your design, so we can make our decision what we like the most. Please see word doc for samples: Text: Law Office Of Marta K. Dolvenidze

Reason: final touches

Target Market(s)

bankruptcy and family law clients

Industry/Entity Type

Family Law

Requirements
Must have
• see examples of law sites
http://promo.lexorbin-example.com/testimonials

- new logo: Law Office of Marta K. Dolvenidze
- client intake form
- blog
- contact us form

Nice to have
• - map
- red color
- on the front page a nice photo of SF or a happy family

```html
<!DOCTYPE html>
<html lang="en">
<head>
<meta charset="utf-8">
<title>Law Office of Marta K. Dolvenidze</title>
<link rel="stylesheet" href="https://fonts.googleapis.com/css2?family=Arimo:wght@400;700&family=Libre+Baskerville:ital,wght@0,400;1,400&family=Open+Sans:wght@400&display=swap">
<style>
  :root {
    --red: #c0101c;
    --red-dark: #9e0c16;
    --gold: #b8860b;
    --gold-light: #f4b400;
    --yellow: #f2c200;
    --ink: #1a1a1a;
    --text: #222;
    --panel: #f5f5f5;
    --dark: #19181c;
    --bar: #2a2830;
    --line: #d8d8d8;
  }
  * { margin: 0; padding: 0; box-sizing: border-box; }
  html, body { width: 825px; height: 1200px; overflow: hidden; background: #fff; }
  body { position: relative; font-family: "Arimo", Arial, sans-serif; color: var(--text); }

  .masthead { position: absolute; left: 0; top: 0; width: 825px; height: 125px; background: linear-gradient(#f9f9f9, #f1f1f1); }
  .brand { position: absolute; top: 26px; left: 0; width: 825px; display: flex; justify-content: center; align-items: center; gap: 12px; }
  .brand-dot { width: 40px; height: 40px; border-radius: 50%; background: var(--red); }
  .brand-name { font-family: "Libre Baskerville", Georgia, serif; font-size: 19px; line-height: 22px; color: var(--red); width: 230px; }
  .lang { position: absolute; left: 98px; top: 104px; display: flex; gap: 3px; }
  .lang span { width: 22px; height: 14px; display: block; }
  .lang .nl { background: linear-gradient(#ae1c28 33%, #fff 33% 66%, #21468b 66%); }
  .lang .en { background: #23306e; position: relative; overflow: hidden; }
  .lang .en::before { content: ""; position: absolute; left: 9px; top: 0; width: 4px; height: 14px; background: #c8102e; box-shadow: 0 0 0 1px #fff; }
  .lang .en::after { content: ""; position: absolute; left: 0; top: 5px; width: 22px; height: 4px; background: #c8102e; box-shadow: 0 0 0 1px #fff; }
  .call { position: absolute; right: 96px; top: 99px; font-family: "Open Sans", Arial, sans-serif; font-size: 18px; color: var(--ink); }
  .call em { font-style: normal; color: var(--red); }

  .nav { position: absolute; left: 96px; top: 125px; width: 633px; height: 25px; background: var(--red); display: flex; }
  .nav a { color: #fff; text-decoration: none; font-size: 10px; line-height: 25px; text-align: center; border-right: 1px solid var(--red-dark); }
  .nav a:last-child { border-right: 0; }

  .hero { position: absolute; left: 96px; top: 150px; width: 633px; height: 295px; background: radial-gradient(ellipse at 75% 45%, #8a5a36 0%, #5a2e1a 40%, #3a1a10 100%); }
  .tab { position: absolute; left: 91px; top: 177px; width: 10px; height: 238px; background: var(--gold); border-radius: 8px 0 0 8px; }
  .profile { position: absolute; left: 96px; top: 202px; width: 161px; height: 188px; background: var(--gold); border-radius: 0 8px 8px 0; }
  .profile .photo { position: absolute; left: 21px; top: 21px; width: 113px; height: 133px; background: linear-gradient(#6b4a3a, #3a2a28); }
  .profile .book { position: absolute; left: 0; top: 162px; width: 156px; text-align: center; color: #fff; font-size: 10.5px; }

  .subscribe { position: absolute; left: 96px; top: 445px; width: 633px; height: 46px; background: var(--bar); }
  .subscribe p { position: absolute; left: 10px; top: 11px; font-family: "Libre Baskerville", Georgia, serif; font-style: italic; font-size: 11px; line-height: 12px; color: #fff; }
  .subscribe p span { color: var(--gold-light); }
  .subscribe .field { position: absolute; left: 388px; top: 15px; width: 173px; height: 17px; background: #fff; font-size: 7px; color: #777; line-height: 17px; padding-left: 4px; }
  .subscribe .submit { position: absolute; left: 565px; top: 15px; width: 59px; height: 17px; background: #f0a000; font-size: 10px; line-height: 17px; text-align: center; color: #222; }

  .welcome { position: absolute; left: 96px; top: 491px; width: 633px; height: 214px; background: var(--panel); padding: 13px 6px 0 5px; }
  .welcome h1 { font-family: "Libre Baskerville", Georgia, serif; font-style: italic; font-weight: 400; font-size: 16px; color: var(--ink); margin-bottom: 10px; }
  .welcome h1 small { font-size: 12px; }
  .welcome h1 span { color: var(--red); }
  .welcome p { font-size: 8.3px; line-height: 12px; margin-bottom: 12px; }
  .welcome h2 { font-family: "Libre Baskerville", Georgia, serif; font-style: italic; font-weight: 400; font-size: 12.5px; margin: 16px 0 8px; }
  .more { font-size: 8.5px; font-weight: 700; color: var(--red); text-decoration: none; }
  .divider { position: absolute; left: 96px; top: 712px; width: 633px; height: 6px; background: radial-gradient(ellipse at top, #bbb, transparent 70%); }

  .practice-title { position: absolute; left: 102px; top: 748px; font-family: "Libre Baskerville", Georgia, serif; font-style: italic; font-size: 16px; color: var(--ink); }
  .practice-title small { font-size: 12px; }
  .view-more { position: absolute; right: 96px; top: 757px; }

  .card { position: absolute; width: 200px; height: 172px; background: var(--dark); }
  .card .pic { height: 125px; }
  .card h3 { position: absolute; left: 6px; top: 131px; font-family: "Libre Baskerville", Georgia, serif; font-weight: 400; font-size: 10.5px; color: var(--yellow); }
  .card .go { position: absolute; right: 0; bottom: 0; width: 55px; height: 17px; background: var(--yellow); clip-path: polygon(10% 0, 100% 0, 100% 100%, 0 100%); font-style: italic; font-size: 8px; line-height: 17px; text-align: right; padding-right: 5px; color: #111; }
  .c1 { left: 96px; } .c2 { left: 313px; } .c3 { left: 529px; }
  .r1 { top: 785px; } .r2 { top: 976px; }

  .footer { position: absolute; left: 96px; top: 1165px; width: 633px; border-top: 1px solid var(--line); padding-top: 10px; display: flex; justify-content: space-between; font-size: 7.5px; color: #555; }
</style>
</head>
<body>
  <header class="masthead">
    <div class="brand"><span class="brand-dot"></span><span class="brand-name">Law Office of Marta K. Dolvenidze</span></div>
    <div class="lang"><span class="nl"></span><span class="en"></span></div>
    <div class="call">CALL <em>41555 0199</em></div>
  </header>

  <nav class="nav">
    <a style="width:69px">HOME</a><a style="width:99px">ABOUT US</a><a style="width:137px">AREA OF PRACTICE</a><a style="width:102px">RESOURCES</a><a style="width:76px">BLOG</a><a style="width:74px">FAQS</a><a style="width:76px">CONTACT</a>
  </nav>

  <div class="hero" role="img" aria-label="Wooden judge's gavel resting on its block on a polished desk"></div>
  <div class="tab"></div>
  <div class="profile">
    <div class="photo" role="img" aria-label="Portrait of the attorney in front of a bookshelf"></div>
    <div class="book">— BOOK AN APPOINTMENT —</div>
  </div>

  <div class="subscribe">
    <p>Subscribe to our news letter for getting latest updates on law<br><span>Bankruptcy and other laws</span></p>
    <div class="field">Type your email id here</div>
    <div class="submit">Submit</div>
  </div>

  <section class="welcome">
    <h1><small>Welcome to</small> KD Law 522 - <span>Complete Bankruptcy Information</span></h1>
    <p>The Law Offices of Marta K. Dolvenidze is a consumer law office dedicated to consumer protection and zealously defending the rights of our clients. We offer the big firm quality legal representation with a small firm individualized attention to each client.</p>
    <p>Our office offers services in: all types of consumer bankruptcy filings, i.e. Chapter 7, Chapter 13, Chapter 11, negotiating a settlement of your debts, assisting you in the defense of collection litigation and defending you against foreclosure. Please review our site and see what we may be able to offer you. Feel free to call us at (415) 555-0199 or use our free case evaluation form.</p>
    <h2>Speak to a Lawyer</h2>
    <p>Unlike some other law firms, when you call the Law Office of Marta K. Dolvenidze you will speak to an actual attorney. Not a paralegal or assistant. And even after retaining our office you will still speak to an attorney unlike other firms where you cannot get a hold of your attorney after several attempts.</p>
    <a class="more">Read more ···· ›</a>
  </section>
  <div class="divider"></div>

  <h2 class="practice-title"><small>see what</small> We are Practicing for You</h2>
  <a class="more view-more">View more ···· ›</a>

  <article class="card c1 r1"><div class="pic" role="img" aria-label="Couple reviewing documents in a law library" style="background:linear-gradient(#6a3a2a,#2a1a14)"></div><h3>DEBT RELIEF</h3><span class="go">View Now</span></article>
  <article class="card c2 r1"><div class="pic" role="img" aria-label="House with a foreclosure sale sign" style="background:linear-gradient(#8fb0d0 40%,#5a7a3a)"></div><h3>FORECLOSURE PREVENTION</h3><span class="go">View Now</span></article>
  <article class="card c3 r1"><div class="pic" role="img" aria-label="Young lawyer in a courtroom" style="background:linear-gradient(#5a2a20,#2a1818)"></div><h3>FAMILY LAW</h3><span class="go">View Now</span></article>
  <article class="card c1 r2"><div class="pic" role="img" aria-label="Broken piggy bank with scattered coins" style="background:linear-gradient(#f4efe6,#e0c8a0)"></div><h3>BANK RUPTCY</h3><span class="go">View Now</span></article>
  <article class="card c2 r2"><div class="pic" role="img" aria-label="Hand stamping an immigration document" style="background:linear-gradient(#2a4a80,#d8d8d8)"></div><h3>IMMIGRATION</h3><span class="go">View Now</span></article>
  <article class="card c3 r2"><div class="pic" role="img" aria-label="Gavel resting on old law books" style="background:linear-gradient(#f0e8d8,#a0703a)"></div><h3>CHAPTER 7, 11, 13 &amp; OTHERS</h3><span class="go">View Now</span></article>

  <footer class="footer">
    <span>Home &nbsp;| About Us &nbsp;| &nbsp;Area of Practice &nbsp;| &nbsp;Resource &nbsp;| &nbsp;FAQs &nbsp;| &nbsp;Blog &nbsp;| &nbsp;Contact Us</span>
    <span>© 2012, KDLaw. All Rights Reserved</span>
  </footer>
</body>
</html>
```